Business Card Design Project

I require a business card with the following information on them for various different people;
name
m:
f:
e:
I have a logo already and will attached that. We are in the construction industry. I require something clean and simple but eye catching at the same time. You can use another colour with our logo if you like and you can style the logo as well if you wish. I am open.
Also it needs to be front and back design.
Industry/Entity Type
Construction
Requirements
Must have
- Logo, name, mobile, fax and email address.
Front and back design

```html
<!DOCTYPE html>
<html lang="en">
<head>
<meta charset="UTF-8">
<title>Halden Ridge Developments – Business Card</title>
<link rel="stylesheet" href="https://fonts.googleapis.com/css2?family=Arimo:wght@400&family=Quicksand:wght@500&display=swap">
<style>
  :root {
    --stage-top: #ffffff;
    --stage-bottom: #d5dcdc;
    --card-white: #ffffff;
    --brand-green: #8ee01a;
    --brand-green-light: #b5f724;
    --brand-green-deep: #7ae60e;
    --text-grey: #5f6a6a;
    --rule-fade: rgba(142, 224, 26, 0);
  }
  * { margin: 0; padding: 0; box-sizing: border-box; }
  html, body {
    width: 1200px;
    height: 1200px;
    overflow: hidden;
  }
  body {
    position: relative;
    background: linear-gradient(to bottom, var(--stage-top) 12%, var(--stage-bottom) 100%);
    font-family: "Arimo", Arial, sans-serif;
  }
  .card {
    position: absolute;
    left: 249px;
    width: 702px;
  }
  .card-front {
    top: 207px;
    height: 373px;
    background: var(--card-white);
  }
  .card-back {
    top: 669px;
    height: 401px;
    background: linear-gradient(to bottom, var(--brand-green-light), var(--brand-green-deep));
  }
  .brand {
    position: absolute;
    display: flex;
    align-items: center;
    gap: 20px;
  }
  .card-front .brand {
    left: 48px;
    top: 42px;
  }
  .brand-square {
    width: 46px;
    height: 46px;
    background: var(--brand-green);
  }
  .brand-name {
    font-family: "Quicksand", "Trebuchet MS", sans-serif;
    font-weight: 500;
    font-size: 40px;
    line-height: 1;
    color: var(--brand-green);
    white-space: nowrap;
  }
  .brand-rule {
    position: absolute;
    left: 48px;
    top: 133px;
    width: 560px;
    height: 3px;
    background: linear-gradient(to right, var(--brand-green) 55%, var(--rule-fade));
  }
  .contact {
    position: absolute;
    left: 60px;
    top: 150px;
    list-style: none;
    color: var(--text-grey);
  }
  .contact-name {
    font-size: 26px;
    color: var(--brand-green);
    margin-bottom: 22px;
    letter-spacing: 0.5px;
  }
  .contact-line {
    font-size: 21px;
    margin-bottom: 26px;
  }
  .contact-label { color: var(--brand-green); }
  .contact-email { font-size: 20px; margin-bottom: 0; }
  .card-back .brand {
    left: 52px;
    bottom: 52px;
  }
  .card-back .brand-square { background: var(--card-white); width: 60px; height: 60px; }
  .card-back .brand-name { color: var(--card-white); font-size: 34px; }
</style>
</head>
<body>
  <section class="card card-front">
    <div class="brand">
      <span class="brand-square"></span>
      <span class="brand-name">Halden Ridge Developments</span>
    </div>
    <div class="brand-rule"></div>
    <ul class="contact">
      <li class="contact-name">Daniel Reyes</li>
      <li class="contact-line"><span class="contact-label">M:</span> 555.014.2738</li>
      <li class="contact-line"><span class="contact-label">F:</span> 555.014.2739</li>
      <li class="contact-line contact-email">DanielReyes@HaldenRidgeDevelopments.com</li>
    </ul>
  </section>

  <section class="card card-back">
    <div class="brand">
      <span class="brand-square"></span>
      <span class="brand-name">Halden Ridge Developments</span>
    </div>
  </section>
</body>
</html>
```